Brand new letterhead, business card, email signature etc.

We are a financial company in London, UK. Our website is www.marlowvane.com. We're wanting a complete remodel of the company colours, letter head, business cards, email signatures, etc. Looking to keep the same font for the company name. I have upload a colour palette that we want to work with. We're looking for company letterhead for outgoing letters/ correspondence, letterhead for internal documentation, email signatures, e-letters. etc. Ultimately we will redesign the entire website also. It is important that our clients get a strong, secure, warm, trustworthy, solid feeling and first impression.
Updates

Designs look the same

Target Market(s)

Institutional investors, (ultra) high net worth individuals

Industry/Entity Type

Finance, Invesments banking.

Font styles to use
Other font styles liked:
• Current font is "Champagne & Limousines"

Requirements
Must have
• Must use the colours provided on the PDF uploaded to the portal. The purple = main colour. The red = accent colour.
Nice to have
• Nice to use same font as now for the company name "Corvane". Font is "Champagne & Limousines". Nice to have some reference to the old logo flower, but only subtle.
Should not have
• Do not use the colour red from our website. Use the colours provided on the colour palette PDF that I uploaded in the portal.

```html
<!DOCTYPE html>
<html lang="en">
<head>
<meta charset="utf-8">
<title>Corvane Stationery</title>
<link href="https://fonts.googleapis.com/css2?family=Quicksand:wght@300;400;500;700&display=swap" rel="stylesheet">
<style>
:root{
  --bg:#d3d3d6;
  --card-dark:#15151b;
  --card-emboss:#24242c;
  --accent:#e0301e;
  --ink:#1d1d22;
  --paper:#f4f4f4;
  --sheet:#ffffff;
  --plum:#1f0a1c;
}
*{margin:0;padding:0;box-sizing:border-box}
html,body{width:1200px;height:792px;overflow:hidden;background:var(--bg)}
body{position:relative;font-family:"Quicksand",sans-serif;color:var(--ink)}
.piece{position:absolute}
.mark{position:absolute;border:1px solid currentColor}
.wordmark{position:absolute;font-family:"Quicksand",sans-serif;font-weight:300;text-transform:uppercase;white-space:nowrap;line-height:1}
.decor{position:absolute}

/* business card front */
.card-front{left:154px;top:233px;width:195px;height:111px;background:var(--card-dark);color:#fff;border-bottom:1px solid var(--accent);overflow:hidden}
.card-front .mark{left:6px;top:5px;width:23px;height:23px;color:#cfcfd4}
.card-front .wordmark{left:34px;top:11px;font-size:12px;letter-spacing:2.4px;color:#e6e6ea}
.card-front .decor{right:0;top:18px;width:86px;height:93px;background:radial-gradient(ellipse at 60% 50%,#22222a 0%,#1a1a20 55%,transparent 80%)}
.card-front .name{position:absolute;left:7px;top:72px;font-size:10px;font-weight:700;white-space:nowrap}
.card-front .name .first{color:var(--accent)}
.card-front .name .role{color:var(--accent);font-weight:400;font-size:6px;margin-left:2px}
.card-front .contacts{position:absolute;left:7px;top:88px;width:181px;font-size:4.8px;display:flex;justify-content:space-between;white-space:nowrap}
.card-front .contacts b{color:var(--accent);font-weight:400}
.card-front .address{position:absolute;left:7px;top:98px;font-size:5.2px;white-space:nowrap}

/* business card back */
.card-back{left:379px;top:233px;width:195px;height:111px;background:var(--card-dark);border-bottom:1px solid var(--accent);color:var(--card-emboss);overflow:hidden}
.card-back .mark{left:25px;top:36px;width:37px;height:37px;border-width:1.5px}
.card-back .wordmark{left:69px;top:46px;font-size:18px;letter-spacing:3px}

/* email signature */
.signature{left:153px;top:401px;width:420px;height:139px;background:var(--sheet);border-bottom:1px solid #f0b5ac;overflow:hidden}
.signature .mark{left:17px;top:46px;width:41px;height:41px;color:var(--ink)}
.signature .wordmark{left:68px;top:58px;font-size:20px;letter-spacing:4px}
.signature .divider{position:absolute;left:210px;top:21px;width:1px;height:95px;background:var(--ink)}
.signature .decor{left:300px;top:0;width:125px;height:139px;background:radial-gradient(ellipse at 45% 50%,#f2f2f4 0%,#f7f7f8 50%,transparent 78%)}
.signature .name{position:absolute;left:231px;top:22px;font-size:14px;font-weight:700;white-space:nowrap}
.signature .name .first{color:var(--accent)}
.signature .title{position:absolute;left:231px;top:39px;font-size:8px;font-weight:500}
.signature .address{position:absolute;left:231px;top:55px;font-size:8px;line-height:10px;font-weight:500}
.signature .lines{position:absolute;left:231px;top:83px;font-size:8px;line-height:10.2px;font-weight:500;list-style:none}
.signature .lines li{display:flex;align-items:center;gap:4px}
.icon{width:7px;height:7px;flex:none}

/* letterhead */
.letterhead{left:595px;top:131px;width:367px;height:519px;background:var(--paper);overflow:hidden}
.letterhead .brand{position:absolute;right:11px;top:8px;display:flex;align-items:center;gap:8px}
.letterhead .brand .mark{position:static;display:block;width:33px;height:33px;color:var(--ink)}
.letterhead .brand .wordmark{position:static;font-size:17px;letter-spacing:3px;margin-right:-3px}
.letterhead .decor{left:48px;top:118px;width:270px;height:290px;background:radial-gradient(ellipse at 55% 50%,#ebebed 0%,#efeff1 45%,transparent 75%)}
.letterhead .footer{position:absolute;left:0;bottom:0;width:367px;height:67px;background:var(--plum);color:#fff}
.letterhead .footer .mark{left:7px;top:7px;width:55px;height:55px;color:#fff}
.letterhead .footer ul{position:absolute;right:12px;top:6px;list-style:none;font-size:7.5px;line-height:10px;text-align:right}
.letterhead .footer li{display:flex;justify-content:flex-end;align-items:center;gap:6px}
.letterhead .footer li.gap{margin-top:6px}
</style>
</head>
<body>

<section class="piece card-front" aria-label="Business card front">
  <span class="mark"></span>
  <span class="wordmark">Corvane</span>
  <div class="decor" role="img" aria-label="Subtle embossed flower decoration"></div>
  <p class="name"><span class="first">Elena</span> Marsh <span class="role">CEO</span></p>
  <p class="contacts"><span><b>T:</b> (020) 7946 0381</span><span><b>E:</b> info@marlowvane.com</span><span><b>W:</b> www.marlowvane.com</span></p>
  <p class="address">18 Harrow Lane, Suite 4, London EC2A 3LT</p>
</section>

<section class="piece card-back" aria-label="Business card back">
  <span class="mark"></span>
  <span class="wordmark">Corvane</span>
</section>

<section class="piece signature" aria-label="Email signature">
  <div class="decor" role="img" aria-label="Faint flower line decoration"></div>
  <span class="mark"></span>
  <span class="wordmark">Corvane</span>
  <span class="divider"></span>
  <p class="name"><span class="first">Elena</span> Marsh</p>
  <p class="title">Managing Director</p>
  <p class="address">18 Harrow Lane, Suite 4<br>London EC2A 3LT</p>
  <ul class="lines">
    <li><svg class="icon" viewBox="0 0 10 10"><path d="M2 1l2 2-1 1.5c.6 1.2 1.4 2 2.5 2.5L7 6l2 2-1.5 1.5C4.5 9 1 5.5.5 2.5z" fill="var(--accent)"/></svg>(020) 7946 0381</li>
    <li><svg class="icon" viewBox="0 0 10 10"><rect x="1" y="2" width="8" height="6" fill="none" stroke="var(--accent)" stroke-width="1.2"/><path d="M1 2l4 3 4-3" fill="none" stroke="var(--accent)" stroke-width="1"/></svg>info@marlowvane.com</li>
    <li><svg class="icon" viewBox="0 0 10 10"><circle cx="5" cy="5" r="4" fill="none" stroke="var(--accent)" stroke-width="1.2"/><path d="M1 5h8M5 1c-2 2.5-2 5.5 0 8M5 1c2 2.5 2 5.5 0 8" fill="none" stroke="var(--accent)" stroke-width=".8"/></svg>www.marlowvane.com</li>
  </ul>
</section>

<section class="piece letterhead" aria-label="Letterhead">
  <div class="brand">
    <span class="mark"></span>
    <span class="wordmark">Corvane</span>
  </div>
  <div class="decor" role="img" aria-label="Blind-embossed flower decoration"></div>
  <footer class="footer">
    <span class="mark"></span>
    <ul>
      <li>27 Aldgate Row<svg class="icon" viewBox="0 0 10 10"><path d="M5 9.5C2.5 6.5 1.5 5 1.5 3.5a3.5 3.5 0 017 0C8.5 5 7.5 6.5 5 9.5z" fill="none" stroke="var(--accent)" stroke-width="1.1"/><circle cx="5" cy="3.6" r="1.2" fill="var(--accent)"/></svg></li>
      <li>London, EC3N 1AB<span class="icon"></span></li>
      <li class="gap">(020) 7946 0381<svg class="icon" viewBox="0 0 10 10"><path d="M2 1l2 2-1 1.5c.6 1.2 1.4 2 2.5 2.5L7 6l2 2-1.5 1.5C4.5 9 1 5.5.5 2.5z" fill="var(--accent)"/></svg></li>
      <li>www.marlowvane.com<svg class="icon" viewBox="0 0 10 10"><circle cx="5" cy="5" r="4" fill="none" stroke="var(--accent)" stroke-width="1.2"/><path d="M1 5h8M5 1c-2 2.5-2 5.5 0 8M5 1c2 2.5 2 5.5 0 8" fill="none" stroke="var(--accent)" stroke-width=".8"/></svg></li>
      <li>info@marlowvane.com<svg class="icon" viewBox="0 0 10 10"><rect x="1" y="2" width="8" height="6" fill="none" stroke="var(--accent)" stroke-width="1.2"/><path d="M1 2l4 3 4-3" fill="none" stroke="var(--accent)" stroke-width="1"/></svg></li>
    </ul>
  </footer>
</section>

</body>
</html>
```